BRIGHTHOLD PROPERTY MANAGEMENT INC. WEBSITE

Please make the website more family-friendly.

I want a website to help me build my property management business by adding listing properties and creating an online application. Im open to any other ideas.
I want a WordPress designer to code it.

Here is my current website. www.brighthold.biz

IDEA: I like the website design https://www.pelicanclimateservices.com/

Thank you

Tom

Number of Pages Required

5+ page

```html
<!DOCTYPE html>
<html lang="en">
<head>
<meta charset="utf-8">
<title>Brighthold Property Management</title>
<link href="https://fonts.googleapis.com/css2?family=Libre+Baskerville:wght@400;700&display=swap" rel="stylesheet">
<style>
:root{
  --red:#b3121b;
  --red-dark:#8e0d14;
  --ink:#1d1d1d;
  --text:#333;
  --white:#fff;
  --line:#d5d5d5;
  --dark:#151515;
  --grey-bg:#f4f4f4;
}
*{box-sizing:border-box;margin:0;padding:0}
html,body{width:1200px;height:4684px;overflow:hidden}
body{position:relative;background:var(--white);font-family:"Libre Baskerville",Georgia,serif;color:var(--text)}
.abs{position:absolute}
.btn{position:absolute;display:flex;align-items:center;justify-content:center;background:var(--red);color:var(--white);font-size:14px;border-radius:5px}
.heading{position:absolute;left:0;width:1200px;display:flex;justify-content:center;align-items:center;gap:14px;font-weight:700;color:var(--ink)}
.heading::before{content:"";width:66px;height:3px;background:var(--red);display:block}
.heading.light{color:var(--white)}
.heading.light::before{background:var(--white)}

/* header */
.site-header{position:absolute;top:0;left:0;width:1200px;height:151px;background:var(--white)}
.brand{position:absolute;display:flex;align-items:center;gap:10px;color:var(--red);font-weight:400;letter-spacing:2px}
.brand .mark{width:34px;height:34px;background:var(--red);display:block}
.search{left:340px;top:22px;width:350px;height:46px;background:#ececec;border-radius:8px;font-size:11px;color:#555;padding:17px 0 0 24px}
.search svg{position:absolute;right:22px;top:14px}
.top-btn{top:20px;height:40px;width:112px;font-size:14px;gap:8px;border-radius:6px}
.main-nav{position:absolute;top:102px;left:388px;display:flex;gap:26px;font-size:13.5px;color:var(--ink)}
.main-nav span::after{content:"";display:inline-block;margin-left:6px;border:5px solid transparent;border-top:6px solid var(--ink);border-bottom:0;vertical-align:middle}

/* hero */
.hero{position:absolute;top:151px;left:0;width:1200px;height:690px;overflow:hidden}
.hero-photo{position:absolute;inset:0;background:linear-gradient(100deg,#3a3f2f 0%,#6f7460 30%,#d9d4cb 55%,#efeae2 80%,#cfc8bd 100%)}
.hero-shade{position:absolute;inset:0;background:linear-gradient(90deg,rgba(0,0,0,.45) 0%,rgba(0,0,0,.2) 45%,rgba(0,0,0,0) 60%)}
.hero-text{position:absolute;left:110px;top:132px;color:var(--white);font-weight:700}
.hero-text .call{font-size:44px;letter-spacing:4px;line-height:60px}
.hero-text .offer{font-size:32px;letter-spacing:3px;line-height:42px;margin-left:4px}
.hero-text .hl{color:var(--red)}

/* about */
.about-copy{position:absolute;top:945px;left:160px;width:880px;text-align:center;font-size:13px;line-height:29.5px;letter-spacing:1px;color:var(--text)}

/* manager */
.manager{position:absolute;top:1275px;left:0;width:1200px;height:563px;background:linear-gradient(90deg,#111 0%,#1e1e1e 50%,#2c2c2c 70%,#f4f4f4 70%)}
.manager-copy{position:absolute;left:115px;top:218px;width:460px;color:var(--white);font-size:12.5px;line-height:27px}
.manager-copy p+p{margin-top:16px}
.manager-title{position:absolute;left:113px;top:58px;color:var(--white);font-size:40px;font-weight:700;line-height:60px}
.manager-title .rule{display:inline-block;width:68px;height:3px;background:var(--white);vertical-align:middle;margin-right:12px}

/* listings */
.card{position:absolute;top:2023px;width:317px;height:422px;background:var(--white);box-shadow:0 2px 8px rgba(0,0,0,.25)}
.card .photo{position:absolute;left:13px;top:15px;width:291px;height:215px}
.card h3{position:absolute;left:13px;top:250px;width:295px;font-size:17px;line-height:27px;font-weight:700;color:var(--ink)}
.card .price{position:absolute;left:16px;font-size:15px;color:var(--red);font-weight:700}
.card .status{position:absolute;right:32px;font-size:15px;color:var(--red);font-weight:700}
.card .specs{position:absolute;left:20px;top:382px;display:flex;align-items:center;gap:10px;font-size:11px;color:#444}
.card .specs .gap{width:22px}
.ribbon{position:absolute;left:672px;top:2005px;width:86px;height:55px;background:var(--red);color:var(--white);font-size:16px;font-weight:700;display:flex;align-items:center;justify-content:center}
.arrow{position:absolute;top:2256px;width:25px;height:25px;border-radius:50%;background:#bbb;display:flex;align-items:center;justify-content:center}

/* applicants */
.applicants{position:absolute;top:2531px;left:0;width:1200px;height:534px;background:linear-gradient(180deg,#2a2a2e 0%,#1b1c20 40%,#2b2722 75%,#151515 100%)}
.app-title{position:absolute;left:0;top:60px;width:1200px;text-align:center;color:var(--white);font-size:42px;font-weight:700;line-height:52px}
.app-title .rule{display:inline-block;width:66px;height:3px;background:var(--white);vertical-align:middle;margin-right:14px}
.feature{position:absolute;top:228px;width:220px;text-align:center}
.feature svg{display:block;margin:0 auto}
.feature span{display:block;margin-top:6px;color:var(--white);font-size:19px;font-weight:700}

/* form */
.field{position:absolute;height:50px;border:1px solid var(--line);font-size:11.5px;color:#444;padding:18px 0 0 16px;background:var(--white)}
.field.select::after{content:"";position:absolute;right:18px;top:20px;width:6px;height:6px;border-right:1.5px solid #444;border-bottom:1.5px solid #444;transform:rotate(45deg)}

/* services */
.services{position:absolute;top:3633px;left:0;width:1200px;height:760px;background:radial-gradient(ellipse at 60% 40%,#3a2a2a 0%,#1c1c1c 55%,#111 100%)}
.pill{position:absolute;height:55px;background:var(--white);border-radius:28px;font-size:16px;font-weight:700;color:var(--ink);display:flex;align-items:center}
.tri{position:absolute}

/* footer */
.footer-links{position:absolute;top:4585px;left:0;width:1200px;display:flex;justify-content:center;font-size:14px;color:var(--ink)}
.footer-links span{padding:0 14px;border-left:2px solid var(--red);line-height:14px}
.footer-links span:first-child{border-left:0}
.copyright{position:absolute;top:4654px;left:0;width:1200px;text-align:center;font-size:11px;color:var(--ink)}
.social{position:absolute;top:4650px;left:917px;display:flex;gap:8px}
.social i{display:block;width:22px;height:22px;background:var(--red);border-radius:3px}
.badge{position:absolute;top:4523px;width:30px;height:30px;border:2px solid var(--ink);border-radius:3px}
</style>
</head>
<body>

<header class="site-header">
  <div class="brand" style="left:112px;top:52px;font-size:28px"><i class="mark"></i>BRIGHTHOLD</div>
  <div class="abs search">Search
    <svg width="18" height="18" viewBox="0 0 18 18"><circle cx="7.5" cy="7.5" r="6" fill="none" stroke="#444" stroke-width="1.8"/><line x1="12" y1="12" x2="17" y2="17" stroke="#444" stroke-width="1.8"/></svg>
  </div>
  <div class="btn top-btn" style="left:732px">
    <svg width="16" height="14" viewBox="0 0 16 14"><path d="M8 0 0 7h2v7h4V9h4v5h4V7h2z" fill="#fff"/></svg>Home</div>
  <div class="btn top-btn" style="left:855px">
    <svg width="16" height="12" viewBox="0 0 16 12"><rect x="0.5" y="0.5" width="15" height="11" fill="none" stroke="#fff"/><path d="M.5.5 8 7 15.5.5" fill="none" stroke="#fff"/></svg>Contact</div>
  <div class="btn top-btn" style="left:976px">
    <svg width="14" height="14" viewBox="0 0 14 14"><circle cx="7" cy="4" r="3.5" fill="#fff"/><path d="M0 14c0-4 3-6 7-6s7 2 7 6z" fill="#fff"/></svg>Login</div>
  <nav class="main-nav">
    <span>Listings</span><span>Owners Prospect</span><span>Tenants</span><span>About</span><span>Community</span><span>Mortgage Info</span>
  </nav>
</header>

<section class="hero">
  <div class="hero-photo" role="img" aria-label="Happy family stepping into the bright entryway of their new rental home"></div>
  <div class="hero-shade"></div>
  <div class="hero-text">
    <div class="call">CALL TODAY</div>
    <div class="offer">Get 1 Month Property</div>
    <div class="offer">Management Fee <span class="hl">Off.</span></div>
    <div class="offer"><span class="hl">$120</span> Value!!</div>
  </div>
  <div class="btn" style="left:113px;top:340px;width:90px;height:38px;font-size:13px">Get Started</div>
  <svg class="abs" style="left:0;top:530px" width="1200" height="160" viewBox="0 0 1200 160">
    <path d="M0 170 L0 175 L1200 175 L1200 170 Z" fill="#fff"/>
    <path d="M0 172 L0 175 L870 175 Z" fill="#fff"/>
    <path d="M0 180 L0 21 L880 135 L1200 30 L1200 180 Z" fill="#fff"/>
    <path d="M0 3 L880 116 L1200 10 L1200 30 L880 135 L0 21 Z" fill="var(--red)"/>
  </svg>
</section>

<h2 class="heading" style="top:875px;font-size:40px">About Us</h2>
<div class="about-copy">
  Our vision for Brighthold Property Management is to provide the best Property Management Services to the Sacramento and surrounding areas. I am focused on providing a more personalized service to you and your tenants. This means we are a one-stop-shop. You only deal with me, no middle guy, so no time is wasted.<br>
  Brighthold Property Management is operated and owned by me Thomas Whitfield I have over 10 years of experience in property management combined with real estate appraising and understand the importance of "return on investment.
</div>
<div class="btn" style="left:543px;top:1147px;width:114px;height:40px">Read More</div>

<section class="manager">
  <div class="abs" role="img" aria-label="Dark blurred rental sign background" style="left:0;top:0;width:640px;height:563px;background:linear-gradient(90deg,rgba(20,20,20,1),rgba(40,30,30,.9))"></div>
  <svg class="abs" style="left:600px;top:0" width="600" height="563" viewBox="0 0 600 563">
    <path d="M242 0 L242 8 L110 8 L10 282 L110 555 L242 555 L242 563 L230 563 L120 563 L0 282 L120 0 Z" fill="#fff"/>
    <path d="M120 22 L600 22 L600 538 L120 538 L28 282 Z" fill="#fff"/>
  </svg>
  <div class="abs" role="img" aria-label="Suburban house with a red For Rent sign on a white post in the front yard" style="left:636px;top:22px;width:564px;height:516px;clip-path:polygon(90px 0,564px 0,564px 516px,90px 516px,0 260px);background:linear-gradient(160deg,#cfdfee 0%,#e6e2d6 35%,#9aa08a 70%,#6c7a4e 100%)"></div>
  <div class="manager-title"><span class="rule"></span>Property Manager for<br>&nbsp;Your Rental</div>
  <div class="manager-copy">
    <p>Vacancy periods are significantly reduced with an extensive pool of prospective renters as well as free advertising.Save on repairs. I have negotiated with maintenance contractors and receive discounts that are passed on to you.</p>
    <p>I perform extensive background checks on prospective renters to minimize your overall vacancy rate and potential non-payments of rent.Regular inspections on your property will be made, inside and out.</p>
  </div>
  <div class="btn" style="left:110px;top:463px;width:112px;height:38px;font-size:13px">Read More</div>
</section>

<h2 class="heading" style="top:1915px;font-size:40px">Our Listings</h2>
<div class="arrow" style="left:44px"><svg width="10" height="10" viewBox="0 0 10 10"><path d="M7 1 3 5l4 4" stroke="#fff" stroke-width="2" fill="none"/></svg></div>
<div class="arrow" style="left:1124px"><svg width="10" height="10" viewBox="0 0 10 10"><path d="M3 1l4 4-4 4" stroke="#fff" stroke-width="2" fill="none"/></svg></div>

<article class="card" style="left:110px">
  <div class="photo" role="img" aria-label="Small beige ADU building beside a large tree" style="background:linear-gradient(180deg,#8fb3d8 0%,#b7c6cf 45%,#b69a72 75%,#8f7a5c 100%)"></div>
  <h3>Fantastic opportunity 2 Bdrm x 1 Bth ADU Unit!!</h3>
  <div class="price" style="top:310px">$2,000.00</div>
  <div class="status" style="top:300px">Available</div>
  <div class="specs">
    <svg width="28" height="18" viewBox="0 0 28 18"><path d="M1 17V3M27 17V9M1 12h26M1 9h26M4 9V5h8v4" stroke="#333" stroke-width="1.6" fill="none"/></svg>2<span class="gap"></span>
    <svg width="26" height="20" viewBox="0 0 26 20"><path d="M1 10h24v3a5 5 0 0 1-5 5H6a5 5 0 0 1-5-5zM4 10V3a2 2 0 0 1 4 0" stroke="#333" stroke-width="1.6" fill="none"/></svg>1<span class="gap"></span>
    <svg width="40" height="10" viewBox="0 0 40 10"><path d="M1 5h38M5 1 1 5l4 4M35 1l4 4-4 4" stroke="#333" stroke-width="1.5" fill="none"/></svg>693 Sq. Ft.
  </div>
</article>

<article class="card" style="left:440px">
  <div class="photo" role="img" aria-label="Bright empty kitchen with white cabinets and a refrigerator" style="background:linear-gradient(180deg,#f2f2f2 0%,#e2e0dc 55%,#8e8a82 80%,#6d6a64 100%)"></div>
  <h3>1840 Maple St. #4</h3>
  <div class="price" style="top:290px">$1,695.00</div>
  <div class="specs">
    <svg width="28" height="18" viewBox="0 0 28 18"><path d="M1 17V3M27 17V9M1 12h26M1 9h26M4 9V5h8v4" stroke="#333" stroke-width="1.6" fill="none"/></svg>3<span class="gap"></span>
    <svg width="26" height="20" viewBox="0 0 26 20"><path d="M1 10h24v3a5 5 0 0 1-5 5H6a5 5 0 0 1-5-5zM4 10V3a2 2 0 0 1 4 0" stroke="#333" stroke-width="1.6" fill="none"/></svg>1<span class="gap"></span>
    <svg width="40" height="10" viewBox="0 0 40 10"><path d="M1 5h38M5 1 1 5l4 4M35 1l4 4-4 4" stroke="#333" stroke-width="1.5" fill="none"/></svg>693 Sq. Ft.
  </div>
</article>
<div class="ribbon">Rented</div>

<article class="card" style="left:770px">
  <div class="photo" role="img" aria-label="Single-story apartment complex among tall green trees" style="background:linear-gradient(180deg,#3f86d6 0%,#7fb2e0 35%,#4f6e3a 60%,#8a8f96 100%)"></div>
  <h3>5217 Linden Ave #3</h3>
  <div class="price" style="top:300px">$1,895.00</div>
  <div class="status" style="top:300px">Available</div>
  <div class="specs" style="top:378px">
    <svg width="26" height="20" viewBox="0 0 26 20"><path d="M1 10h24v3a5 5 0 0 1-5 5H6a5 5 0 0 1-5-5zM4 10V3a2 2 0 0 1 4 0" stroke="#333" stroke-width="1.6" fill="none"/></svg>1<span class="gap"></span>
    <svg width="40" height="10" viewBox="0 0 40 10"><path d="M1 5h38M5 1 1 5l4 4M35 1l4 4-4 4" stroke="#333" stroke-width="1.5" fill="none"/></svg>1,350 Sq. Ft.
  </div>
</article>

<section class="applicants">
  <div class="abs" role="img" aria-label="Modern two-story house lit at dusk" style="inset:0;background:linear-gradient(180deg,rgba(40,40,50,.6),rgba(60,50,35,.5) 70%,rgba(15,15,15,.9))"></div>
  <h2 class="app-title"><span class="rule"></span>Rental Applicants and<br>&nbsp;&nbsp;&nbsp;&nbsp;Prospective Tenants</h2>

  <div class="feature" style="left:53px">
    <svg width="150" height="148" viewBox="0 0 150 148"><path d="M75 2 148 70h-16v76H18V70H2z" fill="#fff"/><circle cx="73" cy="86" r="22" fill="var(--red)"/><text x="73" y="95" font-size="26" text-anchor="middle" fill="#fff" font-family="Georgia,serif" font-weight="700">$</text><path d="M80 112l14-12 8 6 14-16" stroke="var(--red)" stroke-width="5" fill="none"/></svg>
    <span>INCOME</span></div>
  <div class="feature" style="left:272px">
    <svg width="150" height="148" viewBox="0 0 150 148"><path d="M75 2 148 70h-16v76H18V70H2z" fill="#fff"/><rect x="50" y="64" width="40" height="52" rx="3" fill="var(--red)"/><path d="M57 80h18M57 90h26M57 100h26" stroke="#fff" stroke-width="3"/><circle cx="98" cy="72" r="12" fill="var(--red)"/></svg>
    <span>CREDIT REPORTS</span></div>
  <div class="feature" style="left:491px">
    <svg width="150" height="148" viewBox="0 0 150 148"><path d="M75 2 148 70h-16v76H18V70H2z" fill="#fff"/><circle cx="62" cy="80" r="9" fill="var(--red)"/><circle cx="90" cy="96" r="9" fill="var(--red)"/><path d="M76 110c0-10 6-14 14-14s14 4 14 14z" fill="var(--red)"/><path d="M50 96a22 22 0 0 0 20 18M100 84a22 22 0 0 0-20-18" stroke="var(--red)" stroke-width="4" fill="none"/></svg>
    <span>REFERENCES</span></div>
  <div class="feature" style="left:711px">
    <svg width="150" height="148" viewBox="0 0 150 148"><path d="M75 2 148 70h-16v76H18V70H2z" fill="#fff"/><ellipse cx="75" cy="102" rx="17" ry="13" fill="var(--red)"/><circle cx="56" cy="82" r="7" fill="var(--red)"/><circle cx="68" cy="70" r="7" fill="var(--red)"/><circle cx="82" cy="70" r="7" fill="var(--red)"/><circle cx="94" cy="82" r="7" fill="var(--red)"/></svg>
    <span>PETS</span></div>
  <div class="feature" style="left:930px">
    <svg width="150" height="148" viewBox="0 0 150 148"><path d="M75 2 148 70h-16v76H18V70H2z" fill="#fff"/><circle cx="75" cy="72" r="10" fill="var(--red)"/><path d="M58 100c0-12 8-17 17-17s17 5 17 17z" fill="var(--red)"/><circle cx="56" cy="112" r="5" fill="var(--red)"/><circle cx="75" cy="112" r="5" fill="var(--red)"/><path d="M86 110l6 6 12-12" stroke="var(--red)" stroke-width="4" fill="none"/></svg>
    <span>SELECTION PROCESS</span></div>

  <div class="btn" style="left:545px;top:459px;width:111px;height:40px">View All</div>
</section>

<h2 class="heading" style="top:3143px;font-size:40px">Property Information</h2>
<div class="field select" style="left:110px;top:3243px;width:324px">Type Of Property</div>
<div class="field" style="left:440px;top:3243px;width:324px">Number Of Bedrooms</div>
<div class="field" style="left:771px;top:3243px;width:324px">Number Of Bathrooms</div>
<div class="field" style="left:110px;top:3305px;width:324px">Property Address</div>
<div class="field select" style="left:440px;top:3305px;width:324px">City,State</div>
<div class="field" style="left:771px;top:3305px;width:324px">Postal Code</div>
<div class="field" style="left:110px;top:3363px;width:985px;height:122px">Message</div>
<div class="btn" style="left:545px;top:3507px;width:111px;height:40px">Submit</div>

<section class="services">
  <h2 class="heading light" style="top:62px;font-size:40px">Property Management Services</h2>

  <div class="pill" style="left:123px;top:207px;width:280px;padding-left:56px">Rent Collections</div>
  <div class="pill" style="left:115px;top:304px;width:290px;padding-left:8px">Repair &amp; Maintenance Service</div>
  <div class="pill" style="left:180px;top:400px;width:280px;padding-left:40px">Inspection of Property</div>
  <div class="pill" style="left:738px;top:207px;width:337px;padding-left:110px">Leasing</div>
  <div class="pill" style="left:738px;top:304px;width:335px;padding-left:112px">Accounting Services</div>
  <div class="pill" style="left:680px;top:400px;width:338px;padding-left:85px">Security Deposit</div>
  <div class="pill" style="left:443px;top:530px;width:317px;justify-content:center">Mortage &amp; Utility Payments</div>

  <svg class="tri" style="left:0;top:0" width="1200" height="600" viewBox="0 0 1200 600">
    <g fill="var(--red)">
      <path d="M418 195 462 262 372 262Z"/>
      <path d="M420 292 464 359 374 359Z"/>
      <path d="M478 388 522 455 432 455Z"/>
      <path d="M782 195 826 262 736 262Z"/>
      <path d="M782 292 826 359 736 359Z"/>
      <path d="M722 388 766 455 676 455Z"/>
      <path d="M600 474 644 535 556 535Z"/>
    </g>
    <g fill="none" stroke="#fff" stroke-width="3">
      <path d="M406 248v-12l12-10 12 10v12z"/>
      <circle cx="420" cy="338" r="8"/>
      <path d="M466 440v-12l12-10 12 10v12z"/>
      <rect x="770" y="228" width="24" height="18"/>
      <rect x="772" y="324" width="20" height="22"/>
      <circle cx="722" cy="432" r="9"/>
      <path d="M588 522v-12l12-10 12 10v12z"/>
    </g>
    <circle cx="600" cy="313" r="137" fill="#1b1b1b" stroke="#fff" stroke-width="6"/>
    <circle cx="600" cy="313" r="124" fill="none" stroke="#444" stroke-width="3"/>
  </svg>
  <div class="abs" role="img" aria-label="Red model house with a house key tag" style="left:490px;top:203px;width:220px;height:220px;border-radius:50%;background:radial-gradient(circle at 45% 45%,#d8262c 0%,#9d1218 45%,#2a2a2a 72%,#1a1a1a 100%)"></div>
</section>

<svg class="abs" style="left:0;top:4270px" width="1200" height="130" viewBox="0 0 1200 130">
  <path d="M0 95 L320 13 L1200 66 L1200 130 L0 130 Z" fill="#fff"/>
  <path d="M0 0 L1200 0 L1200 48 L320 -5 L0 77 Z" fill="#1a1a1a"/>
  <path d="M0 77 L320 -5 L1200 48 L1200 66 L320 13 L0 95 Z" fill="var(--red)"/>
</svg>

<footer>
  <div class="brand" style="left:0;width:1200px;justify-content:center;top:4440px;font-size:30px"><i class="mark"></i>BRIGHTHOLD</div>
  <i class="badge" style="left:515px"></i>
  <i class="badge" style="left:575px;width:44px"></i>
  <i class="badge" style="left:655px"></i>
  <div class="footer-links">
    <span>Listings</span><span>Owners</span><span>Prospect Tenants</span><span>About</span><span>Community</span><span>Mortgage Info</span>
  </div>
  <div class="abs" style="left:110px;top:4626px;width:975px;height:1px;background:var(--ink)"></div>
  <div class="copyright">Copyright© 2024 BRIGHTHOLD PROPERTY MANAGEMENT INC.</div>
  <div class="social"><i></i><i></i><i></i><i></i><i></i><i></i></div>
</footer>

</body>
</html>
```